Baby Adoption Announcement

I'm looking for a simple, understated and modern baby adoption announcement.

The baby is a boy, but I don't want anything that is blue or particularly boyish. No storks, baby baskets, rattles, or traditional baby announcement designs. No cutesy or busy designs.

Should measure 5.25 x 8.25 inches to fit in an A9 envelope.

Simple graphics MIGHT include birds, grasses, trees, rivers. I'm open to other ideas. Text can be a single color or multi colored. Graphics are not mandatory.

Since this is text heavy, I'd like the designer to be REALLY GOOD at choosing fonts and typesetting.

Text should read:

Memory answers us bright on your face—
Impossibly, we spoke and were silent
Together before all of this. (in italics)

Tobias Aldric Pelt Ostry
Born on March 16, 2012 in Boston, MA
and entrusted to us by his birthmother, Greta.

Named Tobias, which means God is with us, after Greta’s grandfather &
Aldric, after Al and St. Aldric of Myra

Requirements
Must have
• Should measure 5.25 x 8.25 inches to fit in A9 envelope.

Should not have
• The baby is a boy, but I don't want anything that is blue or particularly boyish. No storks, baby baskets, rattles, or traditional baby announcement designs. Nothing cutesy or busy.

```html
<!DOCTYPE html>
<html lang="en">
<head>
<meta charset="utf-8">
<title>Tobias Aldric Pelt Ostry – Adoption Announcement</title>
<link rel="stylesheet" href="https://fonts.googleapis.com/css2?family=Pinyon+Script&family=Sorts+Mill+Goudy&display=swap">
<style>
  :root {
    --backdrop: #e0e9b5;
    --card: #ffffff;
    --panel: #efe4d2;
    --ink: #3f3a3a;
    --accent: #8b2d47;
    --sage: #d6e2ae;
    --blush: #f4ddd6;
    --rose: #e2a9a4;
    --cream: #f5ecd9;
  }
  * { box-sizing: border-box; margin: 0; padding: 0; }
  html, body { width: 1200px; height: 896px; overflow: hidden; background: var(--backdrop); }
  .canvas { position: relative; width: 1200px; height: 896px; overflow: hidden; background: var(--backdrop); }

  .card {
    position: absolute; left: 24px; top: 77px; width: 1149px; height: 744px;
    background: var(--card);
    box-shadow: 2px 4px 10px rgba(0,0,0,0.25);
    overflow: hidden;
  }
  .card-frame {
    position: absolute; left: 12px; top: 18px; width: 1140px; height: 712px;
    border: 7px solid var(--card);
    box-shadow: 0 0 4px rgba(0,0,0,0.18), inset 0 0 4px rgba(0,0,0,0.12);
    z-index: 6;
  }

  .floral-border {
    position: absolute; left: 0; top: 560px; width: 1149px; height: 184px;
    background: linear-gradient(180deg, rgba(244,221,214,0) 0%, var(--blush) 35%, var(--cream) 70%, var(--sage) 100%);
    z-index: 2;
  }
  .branch-bird {
    position: absolute; left: 30px; top: 345px; width: 400px; height: 375px;
    background: radial-gradient(ellipse at 50% 40%, var(--cream) 0%, var(--blush) 55%, rgba(244,221,214,0) 75%);
    z-index: 3;
  }
  .meadow-bloom {
    position: absolute; left: 880px; top: 390px; width: 269px; height: 354px;
    background: radial-gradient(ellipse at 60% 40%, var(--sage) 0%, #e7edc7 55%, rgba(231,237,199,0) 78%);
    z-index: 3;
  }
  .perched-bird {
    position: absolute; left: 509px; top: 57px; width: 153px; height: 87px;
    background: linear-gradient(180deg, var(--rose), #e08a90);
    border-radius: 40px 40px 30px 30px;
    z-index: 5;
  }
  .dragonfly {
    position: absolute; left: 845px; top: 278px; width: 77px; height: 96px;
    background: #ffffff;
    border-radius: 40%;
    box-shadow: 1px 2px 4px rgba(0,0,0,0.25);
    z-index: 5;
  }

  .text-panel {
    position: absolute; left: 291px; top: 101px; width: 585px; height: 537px;
    background: var(--panel);
    border-radius: 62px;
    box-shadow: 3px 5px 10px rgba(0,0,0,0.22);
    z-index: 4;
    text-align: center;
    color: var(--ink);
    font-family: "Sorts Mill Goudy", Georgia, serif;
  }
  .verse {
    position: absolute; left: 0; right: 0; top: 64px;
    font-family: "Pinyon Script", cursive;
    font-size: 31px; line-height: 38px;
  }
  .child-name {
    position: absolute; left: 0; right: 0; top: 216px;
    color: var(--accent);
    font-size: 25px; font-weight: 400; font-variant: small-caps; letter-spacing: 0.5px;
  }
  .birth-details {
    position: absolute; left: 0; right: 0; top: 253px;
    font-size: 20px; line-height: 37px;
  }
  .naming {
    position: absolute; left: 0; right: 0; top: 350px;
    font-size: 20px; line-height: 37px;
  }
  .accent-caps { color: var(--accent); font-variant: small-caps; font-size: 22px; }
  .birthmother { color: var(--accent); font-family: "Pinyon Script", cursive; font-size: 25px; }
</style>
</head>
<body>
<main class="canvas">
  <section class="card">
    <div class="floral-border" role="img" aria-label="Hand-drawn border of blossoms, swirls and seed heads in blush, cream and sage"></div>
    <div class="branch-bird" role="img" aria-label="Illustrated songbird perched on a leafy branch"></div>
    <div class="meadow-bloom" role="img" aria-label="Sage green bloom with starburst flower and dotted tendrils"></div>
    <div class="perched-bird" role="img" aria-label="Small rose-coloured bird with outstretched wings perched on the panel"></div>
    <div class="dragonfly" role="img" aria-label="White dragonfly"></div>

    <article class="text-panel">
      <p class="verse">Memory answers us bright on your face<br>Impossibly, we spoke and were silent<br>Together before all of this</p>
      <h1 class="child-name">Tobias Aldric Pelt Ostry</h1>
      <p class="birth-details">Born on March 16, 2012 in Boston, MA<br>and entrusted to us by his birthmother, <span class="birthmother">Greta</span>.</p>
      <p class="naming">Named Tobias, which means <span class="accent-caps">God is with us</span><br>after Greta’s grandfather &amp;<br><span class="accent-caps">Aldric</span>, after Al and <span class="accent-caps">St. Aldric of Myra</span></p>
    </article>

    <div class="card-frame"></div>
  </section>
</main>
</body>
</html>
```